Advanced Therapeutic Massage Therapist

I need a business card advertising my massage services as an advanced therapeutic massage therapist. I offer advanced therapeutic massage, swedish and deep tissue. I want to create a simple, professional and feminine card. I like bright colours and creativity.

I prefer a bold and experimental approach rather than something status-quo. A card to suggest therapeutic healing through dynamic massage. Motifs, shapes or layout which suggest movement and flow.
Updates

Target Market(s)

Everybody!

Industry/Entity Type

Health And Wellness

Contact Information for Business Card

The card should include:
My name, logo, services offered and my contact details.

Sláine Dunleavy
Massage Therapist

- Swedish - Deep Tissue - Advanced Therapeutic

Phone: (+353) 87 216 4093
Email: regenerate@slainedunleavy-example.com
Website: www.slainedunlevy-example.com

Font styles to use
Serif
Sans Serif
Decorative
Script

Colors

Designer to choose colors to be used in the design.

Requirements
Must have
• An example may contain something like this, yet concise:
• "Sláine Dunleavy
• Massage Therapist
• - Swedish - Deep Tissue - Advanced Therapeutic"
Nice to have
• This sentence is optional:
• Imagery such as a logo or symbol. I have attached a file containing a logo I had produced however the name is incorrect now as it is "Sláine" not "Nelly". It could be edited to change it to Sláine.
• I have sent the file as .psd .jpg. .pdf and .png
• I like when the card conveys energy, movement, pressure points, flow etc.
• I just like the designer to follow their own style and ideas. I like bright colours but must have a lot of a base colour to offset it. I really prefer them to follow their own inspiration. That is my preference.
Should not have
• Pine trees, non-native trees to Britain and Ireland, exotic flowers or animals that are not native to Britain and Ireland.
• I don't like brown as the background colour of the card.
• The cars shouldn't look like a wedding invitation i.e too many floral type designs.

```html
<!DOCTYPE html>
<html lang="en">
<head>
<meta charset="utf-8">
<title>Sláine Dunleavy – Massage Therapist folded card</title>
<link rel="stylesheet" href="https://fonts.googleapis.com/css2?family=Cormorant+Garamond:ital,wght@0,500;1,400;1,500&family=Montserrat:wght@400&display=swap">
<style>
  :root {
    --backdrop: #242322;
    --label: #ffffff;
    --card-white: #ffffff;
    --panel-white: rgba(255,255,255,0.96);
    --teal: #a9dccf;
    --teal-soft: #cdebe3;
    --teal-deep: #7cc5b4;
    --gold: #c98d45;
    --gold-soft: #e3c49c;
    --ink: #3a3330;
    --ink-soft: #5b524d;
    --star: #9fd8c6;
  }
  * { margin: 0; padding: 0; box-sizing: border-box; }
  html, body { width: 1200px; height: 1200px; overflow: hidden; background: var(--backdrop); }
  .canvas { position: relative; width: 1200px; height: 1200px; }
  .side-label {
    position: absolute; left: 0; width: 1200px; text-align: center;
    font-family: 'Montserrat', Arial, sans-serif; font-size: 36px; color: var(--label);
    letter-spacing: 0.5px;
  }
  .side-label--inside { top: 120px; }
  .side-label--outside { top: 666px; }
  .card-shapes { position: absolute; left: 0; top: 0; }

  .text { position: absolute; font-family: 'Cormorant Garamond', 'Times New Roman', serif; color: var(--ink); }
  .center { text-align: center; }

  .brand-name { font-style: normal; font-weight: 500; color: var(--ink-soft); white-space: nowrap; }
  .brand-name--small { left: 236px; width: 200px; top: 408px; font-size: 15px; }
  .brand-name--large { left: 126px; width: 200px; top: 1006px; font-size: 26px; }

  .qualification { left: 116px; width: 442px; top: 437px; font-size: 11px; font-style: italic; font-weight: 500; line-height: 16px; }

  .contact-name { left: 638px; width: 444px; top: 306px; font-size: 22px; font-style: italic; font-weight: 500; }
  .contact-role { left: 638px; width: 444px; top: 334px; font-size: 12px; font-style: italic; }
  .contact-line { left: 638px; width: 444px; font-size: 12px; font-style: italic; display: flex; justify-content: center; align-items: center; gap: 5px; white-space: nowrap; }
  .contact-line--phone { top: 394px; }
  .contact-line--web { top: 414px; }
  .contact-line svg { flex: none; }
  .services-inline { left: 638px; width: 444px; top: 468px; font-size: 12px; font-style: italic; display: flex; justify-content: center; gap: 9px; }
  .star { color: var(--star); font-style: normal; }

  .services-list { left: 800px; width: 300px; top: 918px; text-align: right; font-size: 26px; font-style: italic; line-height: 40px; color: var(--ink-soft); }
  .services-list .star { font-size: 20px; margin-left: 10px; }
</style>
</head>
<body>
<main class="canvas">
  <h2 class="side-label side-label--inside">IN SIDE</h2>
  <h2 class="side-label side-label--outside">OUT SIDE</h2>

  <svg class="card-shapes" width="1200" height="1200" viewBox="0 0 1200 1200">
    <defs>
      <linearGradient id="borderTone" x1="0" y1="0" x2="1" y2="1">
        <stop offset="0" stop-color="#a9dccf"/>
        <stop offset="0.45" stop-color="#c7b48a"/>
        <stop offset="1" stop-color="#9fd3c6"/>
      </linearGradient>
      <radialGradient id="ornamentTone" cx="0.5" cy="0.3" r="0.6">
        <stop offset="0" stop-color="#d9b994"/>
        <stop offset="0.45" stop-color="#cdebe3"/>
        <stop offset="1" stop-color="#ffffff" stop-opacity="0"/>
      </radialGradient>
      <radialGradient id="emblemTone" cx="0.5" cy="0.5" r="0.5">
        <stop offset="0" stop-color="#cdebe3"/>
        <stop offset="1" stop-color="#9fd3c6"/>
      </radialGradient>
    </defs>

    <!-- inside spread -->
    <g class="inside-spread">
      <path class="panel-left" role="img" aria-label="Teal watercolour background with gold swirl pattern"
            d="M76,246 L578,246 Q598,246 598,266 L598,544 L106,544 Q76,544 76,514 Z" fill="url(#borderTone)"/>
      <path class="panel-right" role="img" aria-label="Teal watercolour background with gold swirl pattern"
            d="M620,246 Q600,246 600,266 L600,544 L1090,544 Q1120,544 1120,514 L1120,246 Z" fill="url(#borderTone)"/>
      <rect class="inner-panel" x="116" y="286" width="442" height="218" fill="var(--panel-white)"/>
      <rect class="inner-panel" x="638" y="286" width="444" height="218" fill="var(--panel-white)"/>
      <circle class="brand-circle" cx="336" cy="360" r="34" fill="url(#emblemTone)"/>
      <rect role="img" aria-label="Small teal flourish divider" x="850" y="366" width="28" height="12" rx="6" fill="var(--teal-soft)"/>
      <rect role="img" aria-label="Small teal flourish divider" x="850" y="444" width="28" height="12" rx="6" fill="var(--teal-soft)"/>
    </g>

    <!-- outside spread -->
    <g class="outside-spread">
      <path class="cover" d="M86,764 L586,764 Q600,764 606,778 Q612,764 626,764 L1126,764 L1126,1030 Q1126,1060 1096,1060 L116,1060 Q86,1060 86,1030 Z" fill="var(--card-white)"/>
      <rect role="img" aria-label="Gold and teal mandala-style swirl ornament fading into white"
            x="264" y="764" width="680" height="296" fill="url(#ornamentTone)"/>
      <circle class="brand-circle" cx="226" cy="926" r="68" fill="url(#emblemTone)" stroke="var(--gold-soft)" stroke-width="2"/>
    </g>
  </svg>

  <!-- inside left -->
  <p class="text center brand-name brand-name--small">Nelly Dunleavy</p>
  <p class="text center qualification">IRTB qualified specialising in<br>advanced therapeutic and deep tissue massage</p>

  <!-- inside right -->
  <p class="text center contact-name">Sláine Dunleavy</p>
  <p class="text center contact-role">Massage Therapist</p>
  <p class="text contact-line contact-line--phone">
    <svg width="12" height="10" viewBox="0 0 12 10"><path d="M1,4 Q6,-1 11,4 L9,5 L8,3 L4,3 L3,5 Z M3,6 L9,6 L10,9 L2,9 Z" fill="var(--teal-deep)"/></svg>
    (+353) 87 216 4093
  </p>
  <p class="text contact-line contact-line--web">
    <svg width="11" height="11" viewBox="0 0 12 12"><circle cx="6" cy="6" r="5" fill="none" stroke="var(--teal-deep)" stroke-width="1"/><path d="M1,6 H11 M6,1 Q9,6 6,11 Q3,6 6,1" fill="none" stroke="var(--teal-deep)" stroke-width="1"/></svg>
    www.slainemassage-example.com |
    <svg width="13" height="10" viewBox="0 0 13 10"><rect x="0.5" y="0.5" width="12" height="9" fill="var(--teal-deep)"/><path d="M0.5,0.5 L6.5,5.5 L12.5,0.5" fill="none" stroke="#fff" stroke-width="1"/></svg>
    slainemassage@example.com
  </p>
  <p class="text services-inline"><span>Swedish</span><span class="star">★</span><span>Deep Tissue</span><span class="star">★</span><span>Advanced Therapeutic</span></p>

  <!-- outside -->
  <p class="text center brand-name brand-name--large">Nelly Dunleavy</p>
  <ul class="text services-list" style="list-style:none">
    <li>Swedish<span class="star">★</span></li>
    <li>Deep Tissue<span class="star">★</span></li>
    <li>Advanced Therapeutic<span class="star">★</span></li>
  </ul>
</main>
</body>
</html>
```